Logo, Web and Mobile Designs for enterprise social media platform

All the details are in the attached document, please start reading the scope document first which explains what is this project about and the details about the needed deliverables, after that please read the UI_Requirements document which will detail what is expected regarding the coded web version since this is a coded contest, it is very important that you meet the UI requirements or suggest something else but we will need to agree first before working on the coded version

Good Luck

Target Market(s)

Enterprise Social Media

Industry/Entity Type

Media

Coding

Coded - Design and coding required

Number of Pages Required

5+ page

Font styles to use
Sans Serif

Requirements
Must have
• All the must haves are listed in the scope document so please check before you start

```html
<!DOCTYPE html>
<html lang="en">
<head>
<meta charset="utf-8">
<title>Teamverse – Enterprise Social Platform</title>
<link href="https://fonts.googleapis.com/css2?family=Alfa+Slab+One&family=Roboto:wght@300;400;500;700&display=swap" rel="stylesheet">
<style>
:root{
  --blue:#1ba1d9;
  --green:#7cb42a;
  --orange:#f07b1a;
  --text:#555a5e;
  --heading:#2d2d2d;
  --line:#e1e4e6;
  --muted:#8a8f93;
  --field:#f3f4f5;
  --dark:#2f3133;
  --white:#ffffff;
}
*{box-sizing:border-box;margin:0;padding:0}
html,body{width:1200px;height:2308px;overflow:hidden}
body{position:relative;background:var(--white);font-family:"Roboto",Arial,sans-serif;color:var(--text)}
svg{display:block}

/* header */
.site-header{position:absolute;left:0;top:0;width:1200px;height:92px;background:var(--white)}
.brand{position:absolute;left:74px;top:28px;font-family:"Roboto",Arial,sans-serif;font-weight:700;font-size:28px;color:var(--blue);letter-spacing:.5px;line-height:36px}
.search{position:absolute;left:331px;top:25px;width:238px;height:43px;border:1px solid #d6d9db;display:flex;align-items:center;padding:0 14px;font-size:13px;font-style:italic;color:#9a9ea1;justify-content:space-between}
.main-nav{position:absolute;left:605px;top:38px;display:flex;font-size:13px;font-weight:700;color:var(--heading);letter-spacing:.3px}
.main-nav span{margin-right:34px}
.nav-icon{position:absolute;top:38px}
.badge{position:absolute;top:-12px;left:12px;width:19px;height:19px;border-radius:50%;background:var(--orange);color:var(--white);font-size:10px;font-weight:700;text-align:center;line-height:19px}
.avatar{position:absolute;left:977px;top:24px;width:36px;height:44px;background:linear-gradient(#d9b49a,#8a6a58)}
.user-name{position:absolute;left:1029px;top:39px;font-size:12px;font-weight:500;color:var(--blue);letter-spacing:.3px}
.caret{position:absolute;left:1117px;top:44px}

/* hero */
.hero{position:absolute;left:0;top:92px;width:1200px;height:500px;background:linear-gradient(120deg,#4b3a2e 0%,#7b6656 40%,#a39483 60%,#5e4c3e 100%)}
.hero-shade{position:absolute;inset:0;background:rgba(20,14,10,.35)}
.hero-title{position:absolute;left:0;width:1200px;top:150px;text-align:center;font-family:"Alfa Slab One",Georgia,serif;font-size:56px;font-weight:400;color:var(--white);letter-spacing:2px;line-height:70px}
.hero-text{position:absolute;left:255px;width:690px;top:226px;text-align:center;font-size:26px;font-weight:300;color:var(--white);line-height:34px}
.hero-btn{position:absolute;left:497px;top:325px;width:206px;height:51px;border:2px solid var(--blue);color:var(--white);font-size:19px;font-weight:500;text-align:center;line-height:47px;letter-spacing:.5px}
.hero-arrow{position:absolute;top:205px}
.hero-down{position:absolute;left:585px;top:438px}

/* welcome */
.welcome{position:absolute;left:74px;top:638px;width:1052px}
.section-title{font-size:21px;font-weight:500;color:var(--blue);letter-spacing:.2px}
.welcome p{margin-top:16px;font-size:13.6px;line-height:25.5px;color:var(--text)}
.divider{position:absolute;left:74px;top:792px;width:1052px;height:1px;background:#d5d8da}

/* sidebar */
.widget{position:absolute;left:74px;width:243px;border:1px solid var(--line);background:var(--white)}
.widget-title{padding:14px 14px 0;font-size:16px;font-weight:700;color:var(--blue);line-height:22px;height:50px;border-bottom:1px solid var(--line);letter-spacing:.2px}
.widget-title.tall{height:72px}
.friend{height:79px;border-bottom:1px solid var(--line);display:flex;align-items:center;padding-left:14px;position:relative}
.thumb{width:56px;height:56px;flex:none}
.friend-name{margin-left:18px;font-size:13px;color:var(--heading)}
.online{position:absolute;left:205px;top:32px}
.chat-field{margin:12px 14px 0;height:45px;background:var(--field);border:1px solid #dcdfe1;display:flex;align-items:center;justify-content:space-between;padding:0 14px;font-size:12px;font-style:italic;color:#7d8286}
.email-field{margin:17px 14px 0;height:37px;border:1px solid #dcdfe1;padding:0 12px;font-size:11px;font-style:italic;color:#7d8286;line-height:35px}
.subscribe-btn{position:absolute;right:14px;top:106px;width:96px;height:33px;background:#2b2b2b;color:var(--white);font-size:13px;font-weight:500;text-align:center;line-height:33px;border-radius:2px}
.mini-post{height:80px;border-bottom:1px solid var(--line);position:relative}
.mini-post:last-child{border-bottom:0}
.mini-post .thumb{position:absolute;left:14px;top:14px;width:56px;height:52px}
.mini-text{position:absolute;left:86px;top:10px;width:128px;font-size:12.5px;line-height:18px;color:var(--heading)}
.mini-meta{position:absolute;left:86px;top:50px;display:flex;align-items:center;font-size:11px;color:var(--text);gap:6px}

/* posts */
.featured-title{position:absolute;left:342px;top:824px}
.post{position:absolute;left:342px;width:784px;height:308px;border:1px solid var(--line);background:var(--white)}
.post-tag{position:absolute;left:23px;top:0;width:257px;height:50px;background:var(--green);color:var(--white);font-size:14px;font-weight:700;letter-spacing:.3px;display:flex;align-items:center;justify-content:center;gap:9px;text-transform:uppercase}
.post-media{position:absolute;left:23px;top:66px;width:257px;height:162px}
.play{position:absolute;left:106px;top:59px}
.post-title{position:absolute;left:304px;top:14px;font-size:21px;font-weight:400;color:var(--blue);letter-spacing:.2px}
.post-excerpt{position:absolute;left:304px;top:60px;width:445px;font-size:13px;line-height:22px;color:var(--text)}
.read-more{position:absolute;left:304px;top:188px;width:100px;height:40px;background:#d6d8da;color:#3a3d40;font-size:13px;font-weight:500;text-align:center;line-height:40px;border-radius:2px}
.post-meta{position:absolute;left:0;right:0;top:250px;bottom:0;border-top:1px solid var(--line);display:flex;align-items:center;padding-left:26px;font-size:12.5px;color:#7a7f83}
.post-meta .item{display:flex;align-items:center;gap:8px}
.post-meta .sep{margin:0 20px;color:#9a9ea1}

/* footer */
.site-footer{position:absolute;left:0;top:2211px;width:1200px;height:97px;background:var(--dark)}
.copyright{position:absolute;left:74px;top:42px;font-size:11px;color:var(--white);letter-spacing:.3px}
.social{position:absolute;left:972px;top:38px;display:flex;gap:17px}
.social span{width:18px;height:18px;border-radius:50%;background:var(--white)}
</style>
</head>
<body>

<header class="site-header">
  <div class="brand">TEAMVERSE</div>
  <div class="search">Search..
    <svg width="14" height="14" viewBox="0 0 14 14"><circle cx="6" cy="6" r="4.3" fill="none" stroke="#7cb42a" stroke-width="1.8"/><path d="M9.2 9.2 13 13" stroke="#7cb42a" stroke-width="2"/></svg>
  </div>
  <nav class="main-nav"><span>HOME</span><span>PROFILE</span><span>BLOG</span></nav>
  <div class="nav-icon" style="left:834px">
    <svg width="14" height="15" viewBox="0 0 14 15"><path d="M2 1v14" stroke="#2d2d2d" stroke-width="2"/><path d="M3 1h9l-2 3.5 2 3.5H3z" fill="#2d2d2d"/></svg>
    <span class="badge">0</span>
  </div>
  <div class="nav-icon" style="left:882px">
    <svg width="16" height="13" viewBox="0 0 16 13"><rect x="0" y="1" width="16" height="12" rx="1" fill="#2d2d2d"/><path d="M1 2l7 6 7-6" fill="none" stroke="#fff" stroke-width="1.3"/></svg>
    <span class="badge">0</span>
  </div>
  <div class="nav-icon" style="left:931px">
    <svg width="20" height="15" viewBox="0 0 20 15"><circle cx="7" cy="4" r="3.5" fill="#2d2d2d"/><path d="M0 15c0-5 3-7 7-7s7 2 7 7z" fill="#2d2d2d"/><path d="M16 3v7M12.5 6.5h7" stroke="#2d2d2d" stroke-width="2"/></svg>
  </div>
  <div class="avatar" role="img" aria-label="User profile photo"></div>
  <div class="user-name">USER NAME</div>
  <svg class="caret" width="9" height="6" viewBox="0 0 9 6"><path d="M0 0h9L4.5 6z" fill="#2d2d2d"/></svg>
</header>

<section class="hero">
  <div class="hero-shade" role="img" aria-label="Photo of a hand sketching a social network diagram in a notebook"></div>
  <h1 class="hero-title">SOCIAL MEDIA PLATFORM</h1>
  <p class="hero-text">Vestibulum ante ipsum primis in faucibus orci luctus et ultrices posuere cubilia</p>
  <div class="hero-btn">READ MORE</div>
  <svg class="hero-arrow" style="left:76px" width="28" height="94" viewBox="0 0 28 94"><path d="M26 2 2 47l24 45" fill="none" stroke="#fff" stroke-width="2"/></svg>
  <svg class="hero-arrow" style="left:1098px" width="28" height="94" viewBox="0 0 28 94"><path d="M2 2l24 45L2 92" fill="none" stroke="#fff" stroke-width="2"/></svg>
  <svg class="hero-down" width="30" height="16" viewBox="0 0 30 16"><path d="M2 2l13 12L28 2" fill="none" stroke="#d8d8d8" stroke-width="2.5"/></svg>
</section>

<section class="welcome">
  <h2 class="section-title">WELCOME TO TEAMVERSE</h2>
  <p>Aliquam molestie, mi et imperdiet euismod, dui purus auctor tellus, et interdum lacus lectus et ante. Sed accumsan sollicitudin sapien, sit amet adipiscing turpis gravida ac. In congue, neque ac lobortis volutpat, libero mauris varius mi, vitae suscipit ipsum ligula vitae risus. Duis aliquam nibh a dui iaculis viverra id a velit. Vivamus egestas risus in magna varius commodo. Sed semper viverra egestas. Etiam pretium porttitor lectus, vel ornare neque porta volutpat.</p>
</section>
<div class="divider"></div>

<aside>
  <div class="widget" style="top:831px;height:504px">
    <div class="widget-title">FRIENDS</div>
    <div class="friend"><div class="thumb" role="img" aria-label="Friend photo" style="background:linear-gradient(#c9a58c,#8d6b57)"></div><span class="friend-name">Dan ROE</span><svg class="online" width="12" height="12" viewBox="0 0 12 12"><circle cx="6" cy="6" r="5" fill="none" stroke="#7cb42a" stroke-width="1.3"/><circle cx="6" cy="6" r="2.3" fill="#7cb42a"/></svg></div>
    <div class="friend"><div class="thumb" role="img" aria-label="Friend photo" style="background:linear-gradient(#6b4a3a,#d7b8a4)"></div><span class="friend-name">Dan ROE</span><svg class="online" width="12" height="12" viewBox="0 0 12 12"><circle cx="6" cy="6" r="5" fill="none" stroke="#7cb42a" stroke-width="1.3"/><circle cx="6" cy="6" r="2.3" fill="#7cb42a"/></svg></div>
    <div class="friend"><div class="thumb" role="img" aria-label="Friend photo" style="background:linear-gradient(#a27b62,#5b3f30)"></div><span class="friend-name">Dan ROE</span><svg class="online" width="12" height="12" viewBox="0 0 12 12"><circle cx="6" cy="6" r="5" fill="none" stroke="#7cb42a" stroke-width="1.3"/><circle cx="6" cy="6" r="2.3" fill="#7cb42a"/></svg></div>
    <div class="friend"><div class="thumb" role="img" aria-label="Friend photo" style="background:linear-gradient(#5a3a2c,#d9a68a)"></div><span class="friend-name">Dan ROE</span><svg class="online" width="12" height="12" viewBox="0 0 12 12"><circle cx="6" cy="6" r="5" fill="none" stroke="#7cb42a" stroke-width="1.3"/><circle cx="6" cy="6" r="2.3" fill="#7cb42a"/></svg></div>
    <div class="friend"><div class="thumb" role="img" aria-label="Friend photo" style="background:linear-gradient(#7a5a44,#e6a46a)"></div><span class="friend-name">Dan ROE</span><svg class="online" width="12" height="12" viewBox="0 0 12 12"><circle cx="6" cy="6" r="5" fill="none" stroke="#7cb42a" stroke-width="1.3"/><circle cx="6" cy="6" r="2.3" fill="#7cb42a"/></svg></div>
    <div class="chat-field">Start Chat<svg width="13" height="13" viewBox="0 0 13 13"><path d="M13 0 0 6l5 2 2 5z" fill="#6b7074"/></svg></div>
  </div>

  <div class="widget" style="top:1355px;height:157px">
    <div class="widget-title" style="border-bottom:0;height:auto">SUBSCRIBE TO EVENTS</div>
    <div class="email-field">Enter Email</div>
    <div class="subscribe-btn">Subscribe</div>
  </div>

  <div class="widget" style="top:1529px;height:311px">
    <div class="widget-title tall">PARTICIPATE IN BUSINESS OPPORTUNITIES</div>
    <div class="mini-post"><div class="thumb" role="img" aria-label="Business illustration" style="background:linear-gradient(135deg,#e5a63a,#3a7fb0)"></div><div class="mini-text">Vivamus egestas risus in magna varius..</div><div class="mini-meta"><svg width="11" height="10" viewBox="0 0 11 10"><ellipse cx="5.5" cy="4.3" rx="5.5" ry="4.2" fill="#7cb42a"/><path d="M2 7l-1 3 3-2z" fill="#7cb42a"/></svg>25<span>|</span><svg width="10" height="10" viewBox="0 0 10 10"><rect x="0" y="4" width="2.5" height="6" fill="#7cb42a"/><path d="M3.5 4 6 0c1 0 1.3.8 1 2L6.7 4H10v2.5L8.5 10h-5z" fill="#7cb42a"/></svg>2</div></div>
    <div class="mini-post"><div class="thumb" role="img" aria-label="Business illustration" style="background:linear-gradient(135deg,#d9c3a0,#6d5a48)"></div><div class="mini-text">Vivamus egestas risus in magna varius..</div><div class="mini-meta"><svg width="11" height="10" viewBox="0 0 11 10"><ellipse cx="5.5" cy="4.3" rx="5.5" ry="4.2" fill="#7cb42a"/><path d="M2 7l-1 3 3-2z" fill="#7cb42a"/></svg>25<span>|</span><svg width="10" height="10" viewBox="0 0 10 10"><rect x="0" y="4" width="2.5" height="6" fill="#7cb42a"/><path d="M3.5 4 6 0c1 0 1.3.8 1 2L6.7 4H10v2.5L8.5 10h-5z" fill="#7cb42a"/></svg>2</div></div>
    <div class="mini-post"><div class="thumb" role="img" aria-label="Business illustration" style="background:linear-gradient(135deg,#1f3d55,#5a8a9e)"></div><div class="mini-text">Vivamus egestas risus in magna varius..</div><div class="mini-meta"><svg width="11" height="10" viewBox="0 0 11 10"><ellipse cx="5.5" cy="4.3" rx="5.5" ry="4.2" fill="#7cb42a"/><path d="M2 7l-1 3 3-2z" fill="#7cb42a"/></svg>25<span>|</span><svg width="10" height="10" viewBox="0 0 10 10"><rect x="0" y="4" width="2.5" height="6" fill="#7cb42a"/><path d="M3.5 4 6 0c1 0 1.3.8 1 2L6.7 4H10v2.5L8.5 10h-5z" fill="#7cb42a"/></svg>2</div></div>
  </div>

  <div class="widget" style="top:1861px;height:310px">
    <div class="widget-title">LATEST EVENTS VIDEOS</div>
    <div class="mini-post"><div class="thumb" role="img" aria-label="Event video still" style="background:linear-gradient(135deg,#d2687a,#4a6fb0)"></div><div class="mini-text">Vivamus egestas risus in magna varius..</div><div class="mini-meta"><svg width="11" height="10" viewBox="0 0 11 10"><ellipse cx="5.5" cy="4.3" rx="5.5" ry="4.2" fill="#7cb42a"/><path d="M2 7l-1 3 3-2z" fill="#7cb42a"/></svg>25<span>|</span><svg width="10" height="10" viewBox="0 0 10 10"><rect x="0" y="4" width="2.5" height="6" fill="#7cb42a"/><path d="M3.5 4 6 0c1 0 1.3.8 1 2L6.7 4H10v2.5L8.5 10h-5z" fill="#7cb42a"/></svg>2</div></div>
    <div class="mini-post"><div class="thumb" role="img" aria-label="Event video still" style="background:linear-gradient(135deg,#1a1f3a,#b0582c)"></div><div class="mini-text">Vivamus egestas risus in magna varius..</div><div class="mini-meta"><svg width="11" height="10" viewBox="0 0 11 10"><ellipse cx="5.5" cy="4.3" rx="5.5" ry="4.2" fill="#7cb42a"/><path d="M2 7l-1 3 3-2z" fill="#7cb42a"/></svg>25<span>|</span><svg width="10" height="10" viewBox="0 0 10 10"><rect x="0" y="4" width="2.5" height="6" fill="#7cb42a"/><path d="M3.5 4 6 0c1 0 1.3.8 1 2L6.7 4H10v2.5L8.5 10h-5z" fill="#7cb42a"/></svg>2</div></div>
    <div class="mini-post"><div class="thumb" role="img" aria-label="Event video still" style="background:linear-gradient(135deg,#c7d3de,#3d6f9c)"></div><div class="mini-text">Vivamus egestas risus in magna varius..</div><div class="mini-meta"><svg width="11" height="10" viewBox="0 0 11 10"><ellipse cx="5.5" cy="4.3" rx="5.5" ry="4.2" fill="#7cb42a"/><path d="M2 7l-1 3 3-2z" fill="#7cb42a"/></svg>25<span>|</span><svg width="10" height="10" viewBox="0 0 10 10"><rect x="0" y="4" width="2.5" height="6" fill="#7cb42a"/><path d="M3.5 4 6 0c1 0 1.3.8 1 2L6.7 4H10v2.5L8.5 10h-5z" fill="#7cb42a"/></svg>2</div></div>
  </div>
</aside>

<h2 class="section-title featured-title">FEATURED POSTS</h2>

<article class="post" style="top:881px">
  <div class="post-tag"><svg width="12" height="13" viewBox="0 0 12 13"><circle cx="6" cy="3.3" r="3.3" fill="#fff"/><path d="M0 13c0-4 2.5-6 6-6s6 2 6 6z" fill="#fff"/></svg>Business Opportunities</div>
  <div class="post-media" role="img" aria-label="Photo of hands holding social media signs around a table" style="background:linear-gradient(135deg,#c9b48f,#3e8fa8 55%,#d7a040)"></div>
  <h3 class="post-title">Aenean a nibh eget turpis vehicula tempus</h3>
  <p class="post-excerpt">Aliquam molestie, mi et imperdiet euismod, dui purus auctor tellus, et interdum lacus lectus et ante. Sed accumsan sollicitudin sapien, sit amet adipiscing turpis gravida ac. In congue, neque ac lobortis volutpat, libero mauris varius mi, vitae suscipit ipsum ligula vitae risus. Vivamus egestas risus in magna varius commodo. Sed semper viverra egestas.</p>
  <div class="read-more">Read More</div>
  <div class="post-meta">
    <span class="item"><svg width="10" height="11" viewBox="0 0 12 13"><circle cx="6" cy="3.3" r="3.3" fill="#7cb42a"/><path d="M0 13c0-4 2.5-6 6-6s6 2 6 6z" fill="#7cb42a"/></svg>By Admin</span><span class="sep">|</span>
    <span class="item"><svg width="11" height="11" viewBox="0 0 11 11"><rect x="0" y="1.5" width="11" height="9.5" fill="#7cb42a"/><rect x="1.5" y="4.5" width="8" height="5" fill="#fff"/></svg>Posted on</span><span class="sep">|</span>
    <span class="item"><svg width="12" height="11" viewBox="0 0 11 10"><ellipse cx="5.5" cy="4.3" rx="5.5" ry="4.2" fill="#7cb42a"/><path d="M2 7l-1 3 3-2z" fill="#7cb42a"/></svg>Comments</span><span class="sep">|</span>
    <span class="item"><svg width="11" height="11" viewBox="0 0 10 10"><rect x="0" y="4" width="2.5" height="6" fill="#7cb42a"/><path d="M3.5 4 6 0c1 0 1.3.8 1 2L6.7 4H10v2.5L8.5 10h-5z" fill="#7cb42a"/></svg>Like</span><span class="sep">|</span>
    <span class="item"><svg width="11" height="11" viewBox="0 0 11 11"><circle cx="2.2" cy="5.5" r="2.2" fill="#7cb42a"/><circle cx="8.8" cy="2.2" r="2.2" fill="#7cb42a"/><circle cx="8.8" cy="8.8" r="2.2" fill="#7cb42a"/><path d="M2.2 5.5l6.6-3.3M2.2 5.5l6.6 3.3" stroke="#7cb42a" stroke-width="1.3"/></svg>Share</span>
  </div>
</article>

<article class="post" style="top:1208px">
  <div class="post-tag"><svg width="12" height="12" viewBox="0 0 11 11"><rect x="0" y="1.5" width="11" height="9.5" fill="#fff"/><rect x="1.5" y="4.5" width="8" height="5" fill="#7cb42a"/></svg>Events</div>
  <div class="post-media" role="img" aria-label="Photo of performers on a lit concert stage" style="background:linear-gradient(180deg,#1b2a5a,#3a4f9a 45%,#b2443a)"><svg class="play" width="44" height="44" viewBox="0 0 44 44"><circle cx="22" cy="22" r="19" fill="none" stroke="#fff" stroke-width="3"/><path d="M17 13l13 9-13 9z" fill="#fff"/></svg></div>
  <h3 class="post-title">Aenean a nibh eget turpis vehicula tempus</h3>
  <p class="post-excerpt">Aliquam molestie, mi et imperdiet euismod, dui purus auctor tellus, et interdum lacus lectus et ante. Sed accumsan sollicitudin sapien, sit amet adipiscing turpis gravida ac. In congue, neque ac lobortis volutpat, libero mauris varius mi, vitae suscipit ipsum ligula vitae risus. Vivamus egestas risus in magna varius commodo. Sed semper viverra egestas.</p>
  <div class="read-more">Read More</div>
  <div class="post-meta">
    <span class="item"><svg width="10" height="11" viewBox="0 0 12 13"><circle cx="6" cy="3.3" r="3.3" fill="#7cb42a"/><path d="M0 13c0-4 2.5-6 6-6s6 2 6 6z" fill="#7cb42a"/></svg>By Admin</span><span class="sep">|</span>
    <span class="item"><svg width="11" height="11" viewBox="0 0 11 11"><rect x="0" y="1.5" width="11" height="9.5" fill="#7cb42a"/><rect x="1.5" y="4.5" width="8" height="5" fill="#fff"/></svg>Posted on</span><span class="sep">|</span>
    <span class="item"><svg width="12" height="11" viewBox="0 0 11 10"><ellipse cx="5.5" cy="4.3" rx="5.5" ry="4.2" fill="#7cb42a"/><path d="M2 7l-1 3 3-2z" fill="#7cb42a"/></svg>Comments</span><span class="sep">|</span>
    <span class="item"><svg width="11" height="11" viewBox="0 0 10 10"><rect x="0" y="4" width="2.5" height="6" fill="#7cb42a"/><path d="M3.5 4 6 0c1 0 1.3.8 1 2L6.7 4H10v2.5L8.5 10h-5z" fill="#7cb42a"/></svg>Like</span><span class="sep">|</span>
    <span class="item"><svg width="11" height="11" viewBox="0 0 11 11"><circle cx="2.2" cy="5.5" r="2.2" fill="#7cb42a"/><circle cx="8.8" cy="2.2" r="2.2" fill="#7cb42a"/><circle cx="8.8" cy="8.8" r="2.2" fill="#7cb42a"/><path d="M2.2 5.5l6.6-3.3M2.2 5.5l6.6 3.3" stroke="#7cb42a" stroke-width="1.3"/></svg>Share</span>
  </div>
</article>

<article class="post" style="top:1534px">
  <div class="post-tag"><svg width="16" height="12" viewBox="0 0 16 12"><circle cx="8" cy="3" r="3" fill="#fff"/><circle cx="2.8" cy="4.3" r="2" fill="#fff"/><circle cx="13.2" cy="4.3" r="2" fill="#fff"/><path d="M3 12c0-4 2-5.5 5-5.5s5 1.5 5 5.5z" fill="#fff"/><path d="M0 11c0-3 1-4 3-4l1 4zM16 11c0-3-1-4-3-4l-1 4z" fill="#fff"/></svg>Networks</div>
  <div class="post-media" role="img" aria-label="Photo of a group of friends looking at a phone" style="background:linear-gradient(135deg,#d9c2ae,#9a6e52 50%,#e3d3c6)"></div>
  <h3 class="post-title">Aenean a nibh eget turpis vehicula tempus</h3>
  <p class="post-excerpt">Aliquam molestie, mi et imperdiet euismod, dui purus auctor tellus, et interdum lacus lectus et ante. Sed accumsan sollicitudin sapien, sit amet adipiscing turpis gravida ac. In congue, neque ac lobortis volutpat, libero mauris varius mi, vitae suscipit ipsum ligula vitae risus. Vivamus egestas risus in magna varius commodo. Sed semper viverra egestas.</p>
  <div class="read-more">Read More</div>
  <div class="post-meta">
    <span class="item"><svg width="10" height="11" viewBox="0 0 12 13"><circle cx="6" cy="3.3" r="3.3" fill="#7cb42a"/><path d="M0 13c0-4 2.5-6 6-6s6 2 6 6z" fill="#7cb42a"/></svg>By Admin</span><span class="sep">|</span>
    <span class="item"><svg width="11" height="11" viewBox="0 0 11 11"><rect x="0" y="1.5" width="11" height="9.5" fill="#7cb42a"/><rect x="1.5" y="4.5" width="8" height="5" fill="#fff"/></svg>Posted on</span><span class="sep">|</span>
    <span class="item"><svg width="12" height="11" viewBox="0 0 11 10"><ellipse cx="5.5" cy="4.3" rx="5.5" ry="4.2" fill="#7cb42a"/><path d="M2 7l-1 3 3-2z" fill="#7cb42a"/></svg>Comments</span><span class="sep">|</span>
    <span class="item"><svg width="11" height="11" viewBox="0 0 10 10"><rect x="0" y="4" width="2.5" height="6" fill="#7cb42a"/><path d="M3.5 4 6 0c1 0 1.3.8 1 2L6.7 4H10v2.5L8.5 10h-5z" fill="#7cb42a"/></svg>Like</span><span class="sep">|</span>
    <span class="item"><svg width="11" height="11" viewBox="0 0 11 11"><circle cx="2.2" cy="5.5" r="2.2" fill="#7cb42a"/><circle cx="8.8" cy="2.2" r="2.2" fill="#7cb42a"/><circle cx="8.8" cy="8.8" r="2.2" fill="#7cb42a"/><path d="M2.2 5.5l6.6-3.3M2.2 5.5l6.6 3.3" stroke="#7cb42a" stroke-width="1.3"/></svg>Share</span>
  </div>
</article>

<article class="post" style="top:1861px">
  <div class="post-tag"><svg width="12" height="12" viewBox="0 0 11 11"><rect x="0" y="1.5" width="11" height="9.5" fill="#fff"/><rect x="1.5" y="4.5" width="8" height="5" fill="#7cb42a"/></svg>Events</div>
  <div class="post-media" role="img" aria-label="Photo of a cheering crowd at a party" style="background:linear-gradient(135deg,#3f5f7a,#c46a8e 45%,#e0b04a)"><svg class="play" width="44" height="44" viewBox="0 0 44 44"><circle cx="22" cy="22" r="19" fill="none" stroke="#fff" stroke-width="3"/><path d="M17 13l13 9-13 9z" fill="#fff"/></svg></div>
  <h3 class="post-title">Aenean a nibh eget turpis vehicula tempus</h3>
  <p class="post-excerpt">Aliquam molestie, mi et imperdiet euismod, dui purus auctor tellus, et interdum lacus lectus et ante. Sed accumsan sollicitudin sapien, sit amet adipiscing turpis gravida ac. In congue, neque ac lobortis volutpat, libero mauris varius mi, vitae suscipit ipsum ligula vitae risus. Vivamus egestas risus in magna varius commodo. Sed semper viverra egestas.</p>
  <div class="read-more">Read More</div>
  <div class="post-meta">
    <span class="item"><svg width="10" height="11" viewBox="0 0 12 13"><circle cx="6" cy="3.3" r="3.3" fill="#7cb42a"/><path d="M0 13c0-4 2.5-6 6-6s6 2 6 6z" fill="#7cb42a"/></svg>By Admin</span><span class="sep">|</span>
    <span class="item"><svg width="11" height="11" viewBox="0 0 11 11"><rect x="0" y="1.5" width="11" height="9.5" fill="#7cb42a"/><rect x="1.5" y="4.5" width="8" height="5" fill="#fff"/></svg>Posted on</span><span class="sep">|</span>
    <span class="item"><svg width="12" height="11" viewBox="0 0 11 10"><ellipse cx="5.5" cy="4.3" rx="5.5" ry="4.2" fill="#7cb42a"/><path d="M2 7l-1 3 3-2z" fill="#7cb42a"/></svg>Comments</span><span class="sep">|</span>
    <span class="item"><svg width="11" height="11" viewBox="0 0 10 10"><rect x="0" y="4" width="2.5" height="6" fill="#7cb42a"/><path d="M3.5 4 6 0c1 0 1.3.8 1 2L6.7 4H10v2.5L8.5 10h-5z" fill="#7cb42a"/></svg>Like</span><span class="sep">|</span>
    <span class="item"><svg width="11" height="11" viewBox="0 0 11 11"><circle cx="2.2" cy="5.5" r="2.2" fill="#7cb42a"/><circle cx="8.8" cy="2.2" r="2.2" fill="#7cb42a"/><circle cx="8.8" cy="8.8" r="2.2" fill="#7cb42a"/><path d="M2.2 5.5l6.6-3.3M2.2 5.5l6.6 3.3" stroke="#7cb42a" stroke-width="1.3"/></svg>Share</span>
  </div>
</article>

<footer class="site-footer">
  <div class="copyright">COPYRIGHT © 2015.COMPANYNAME.ALL RIGHT RESERVED</div>
  <div class="social" aria-label="Social links">
    <span role="img" aria-label="Social link"></span>
    <span role="img" aria-label="Social link"></span>
    <span role="img" aria-label="Social link"></span>
    <span role="img" aria-label="Social link"></span>
    <span role="img" aria-label="Feed link"></span>
  </div>
</footer>

</body>
</html>
```